Letterhead and matching envelope design for a dental office

We need a new stationary design, letterhead and envelope #10, for a dental office in Denver area. We are called Bright Harbor Dental. We want a simple and minimalistic design but not a boring design. I wish to have one good point that makes it look professional. I have attached our logo. Feel free to use either one. I want the design for letterhead and envelope look like a "matching pair" but not look the same. The envelope doesn't have to be white and it will have an address window on bottom left.

Target Market(s)

everyone who visits dentist (adults)

Industry/Entity Type

Dental

Font styles to use
Other font styles liked:
• close to font on logo or something that matches well

Requirements
Must have
• professional
• simple, minimalistic
• unique point that stands out
Nice to have
• matching but not same design for letterhead and envelope
Should not have
• not look like all the other boring designs
• no flowery, distracting feats

```html
<!DOCTYPE html>
<html lang="en">
<head>
<meta charset="utf-8">
<title>Bright Harbor Dental — Letterhead</title>
<link rel="stylesheet" href="https://fonts.googleapis.com/css2?family=Arimo:wght@400;700&display=swap">
<style>
  :root {
    --backdrop: #e9e9ea;
    --paper: #ffffff;
    --brand-green: #3cb44a;
    --brand-green-light: #a9d9a1;
    --brand-green-pale: #eef6ec;
    --ink: #2b2b2b;
    --ink-soft: #444444;
    --on-green: #ffffff;
  }
  * { box-sizing: border-box; margin: 0; padding: 0; }
  html, body {
    width: 1200px; height: 795px; overflow: hidden;
    background: var(--backdrop);
    font-family: "Arimo", Arial, sans-serif;
  }
  .canvas {
    position: relative; width: 1200px; height: 795px;
  }
  .letterhead {
    position: absolute; left: 320px; top: 26px;
    width: 560px; height: 743px;
    background: var(--paper);
    box-shadow: 0 6px 18px rgba(0,0,0,0.12);
    overflow: hidden;
  }
  .letterhead__artwork {
    position: absolute; inset: 0; width: 100%; height: 100%;
  }
  .brand {
    position: absolute; top: 52px; left: 0; right: 0;
    display: flex; justify-content: center; align-items: center; gap: 8px;
  }
  .brand__dot {
    width: 10px; height: 10px; border-radius: 50%;
    background: var(--brand-green);
  }
  .brand__name {
    color: var(--brand-green);
    font-size: 15px; font-weight: 700;
    letter-spacing: 0.14em; text-transform: uppercase;
  }
  .letter {
    position: absolute; top: 190px; left: 52px; width: 440px;
    color: var(--ink-soft);
    font-size: 9.5px; line-height: 1.45;
  }
  .letter__salutation {
    color: var(--ink); font-weight: 700; font-size: 11px;
    margin-bottom: 12px;
  }
  .letter__paragraph { margin-bottom: 11px; }
  .signature {
    width: 110px; height: 36px; margin-top: 14px;
    background: linear-gradient(90deg, #e4e4e4, #f4f4f4);
    border-radius: 4px;
  }
  .contact {
    position: absolute; right: 22px; bottom: 24px;
    list-style: none; text-align: right;
    color: var(--on-green); font-size: 9px; line-height: 1.9;
  }
  .contact__item {
    display: flex; justify-content: flex-end; align-items: center; gap: 6px;
  }
  .contact__icon {
    width: 11px; height: 11px; border-radius: 50%;
    background: var(--on-green);
    display: inline-flex; align-items: center; justify-content: center;
  }
</style>
</head>
<body>
<main class="canvas">
  <article class="letterhead">
    <svg class="letterhead__artwork" viewBox="0 0 560 743" preserveAspectRatio="none" aria-hidden="true">
      <ellipse role="img" aria-label="Faint brand decoration area" cx="330" cy="540" rx="120" ry="150" fill="var(--brand-green-pale)"/>
      <path d="M150 743 C 330 680, 470 560, 560 395 L 560 743 Z" fill="var(--brand-green-light)"/>
      <path d="M200 743 C 360 690, 490 590, 560 430 L 560 743 Z" fill="#d3ecce"/>
      <path d="M230 743 C 380 700, 500 610, 560 455 L 560 743 Z" fill="var(--brand-green)"/>
    </svg>

    <header class="brand">
      <span class="brand__dot"></span>
      <span class="brand__name">Bright Harbor Dental</span>
    </header>

    <section class="letter">
      <p class="letter__salutation">Dear Mr. Ellis,</p>
      <p class="letter__paragraph">Lorem Ipsum is simply dummy text of the printing and typesetting industry. Lorem Ipsum has been the industry's standard dummy text ever since the 1500s, when an unknown printer took a galley of type and scrambled it to make a type specimen book. It has survived not only five centuries, but also the leap into electronic typesetting, remaining essentially unchanged.</p>
      <p class="letter__paragraph">The standard chunk of Lorem Ipsum used since the 1500s is reproduced below for those interested. Sections 1.10.32 and 1.10.33 from "de Finibus Bonorum et Malorum" by Cicero are also reproduced in their exact original form, accompanied by English versions from the 1914 translation by H. Rackham.</p>
      <p class="letter__paragraph">Lorem Ipsum is simply dummy text of the printing and typesetting industry. Lorem Ipsum has been the industry's standard dummy text ever since the 1500s, when an unknown printer took a galley of type and scrambled it to make a type specimen book. It has survived not only five centuries, but also the leap into electronic typesetting, remaining essentially unchanged. It was popularised in the</p>
      <div class="signature" role="img" aria-label="Handwritten signature"></div>
    </section>

    <ul class="contact">
      <li class="contact__item">720-555-0142
        <span class="contact__icon"><svg width="7" height="7" viewBox="0 0 10 10"><path d="M2 1 L4 1 L4.6 3.2 L3.4 4 C4 5.4 4.8 6.2 6 6.7 L6.8 5.5 L9 6.1 L9 8 C5 8.6 1.4 5 2 1 Z" fill="var(--brand-green)"/></svg></span></li>
      <li class="contact__item">info@brightharbordental.com
        <span class="contact__icon"><svg width="7" height="7" viewBox="0 0 10 10"><rect x="1" y="2.5" width="8" height="5.5" fill="none" stroke="var(--brand-green)" stroke-width="1.2"/><path d="M1 2.5 L5 5.5 L9 2.5" fill="none" stroke="var(--brand-green)" stroke-width="1.2"/></svg></span></li>
      <li class="contact__item">www.brightharbordental.com
        <span class="contact__icon"><svg width="7" height="7" viewBox="0 0 10 10"><circle cx="5" cy="5" r="3.8" fill="none" stroke="var(--brand-green)" stroke-width="1.2"/><path d="M1.2 5 H8.8" stroke="var(--brand-green)" stroke-width="1"/></svg></span></li>
      <li class="contact__item">2210 Larkspur Ave Suite 150 Westminster, CO 80031
        <span class="contact__icon"><svg width="7" height="7" viewBox="0 0 10 10"><path d="M5 9.5 C2.5 6.5 2 5 2 4 A3 3 0 0 1 8 4 C8 5 7.5 6.5 5 9.5 Z" fill="var(--brand-green)"/></svg></span></li>
    </ul>
  </article>
</main>
</body>
</html>
```